Volbrey Inc Business Card

Looking to get an updated business card for a Contract Machining company (www.volbreyinc.example) - looking for a clean design the portrays the technical nature of the business - colors can follow the website design and be in any combination that makes sense (red black, white, metallic or silver) - logos attached for use also. Would like space for: Name, title, business phone (555 214-3086), cell phone , website (www.volbreyinc.example) - possibly QR code could be integrated for website (designer choice), business address - 418 Harlow Bend, Ashcombe, NR 48199 (cards will be for 4 employees, I will either need to modify a template or I can provide individual information)
Target Market(s)
Aerospace, defense and medical device manufacturing companies that need machining
Industry/Entity Type
Machining for aerospace, defense, medical
Contact Information for Business Card
Name, Title, Business Phone, Cell Phone, email, business website and business address
Look and feel

```html
<!DOCTYPE html>
<html lang="en">
<head>
<meta charset="utf-8">
<title>Volbrey Inc Business Card</title>
<link href="https://fonts.googleapis.com/css2?family=Montserrat:wght@500;700;800&family=Arimo:wght@400&display=swap" rel="stylesheet">
<style>
  :root {
    --stage: #3d3d3d;
    --brand-red: #b01f24;
    --paper: #ffffff;
    --card-w: 520px;
    --card-h: 297px;
  }
  * { margin: 0; padding: 0; box-sizing: border-box; }
  html, body { width: 1200px; height: 803px; overflow: hidden; background: var(--stage); }
  .stage {
    width: 1200px; height: 803px;
    display: flex; align-items: center; justify-content: center; gap: 60px;
  }
  .card {
    width: var(--card-w); height: var(--card-h);
    border-radius: 18px; position: relative; overflow: hidden;
    box-shadow: 0 14px 30px rgba(0,0,0,.35);
  }
  .card--front { background: var(--brand-red); color: var(--paper); }
  .card--back { background: var(--paper); }

  .front__disc {
    position: absolute; left: 240px; top: 14px;
    width: 270px; height: 270px; border-radius: 50%;
    background: var(--paper);
  }
  .front__info { position: absolute; left: 32px; top: 36px; width: 200px; }
  .brand-name {
    font-family: "Montserrat", sans-serif; font-weight: 800;
    letter-spacing: 1px; text-transform: uppercase; white-space: nowrap;
  }
  .front__info .brand-name { font-size: 22px; color: var(--paper); }
  .person__name {
    font-family: "Montserrat", sans-serif; font-weight: 700;
    font-size: 18px; margin-top: 28px; white-space: nowrap;
  }
  .person__title { font-family: "Arimo", sans-serif; font-size: 11px; margin-top: 1px; }
  .address {
    font-family: "Arimo", sans-serif; font-size: 11px; line-height: 15px;
    font-style: normal; margin-top: 18px; white-space: nowrap;
  }
  .contact-list { list-style: none; margin-top: 14px; }
  .contact-list li {
    font-family: "Arimo", sans-serif; font-size: 11px; line-height: 16px;
    display: flex; align-items: center; gap: 7px; white-space: nowrap;
  }
  .contact-list svg { width: 10px; height: 10px; flex: none; }

  .back__mark {
    position: absolute; left: 50%; top: 62px; transform: translateX(-50%);
    width: 118px; height: 118px; border-radius: 50%; background: var(--brand-red);
  }
  .back__name {
    position: absolute; left: 0; right: 0; top: 194px; text-align: center;
    font-size: 26px; color: var(--brand-red);
  }
</style>
</head>
<body>
<main class="stage">
  <section class="card card--front" aria-label="Card front">
    <div class="front__info">
      <div class="brand-name">Volbrey Inc</div>
      <div class="person__name">Dana Whitlock</div>
      <div class="person__title">President</div>
      <address class="address">418 Harlow Bend<br>Ashcombe, NR 48199</address>
      <ul class="contact-list">
        <li><svg viewBox="0 0 10 10"><path d="M2 1l2 2-1 1.2c.6 1.3 1.5 2.2 2.8 2.8L7 6l2 2-1.3 1.5C4.5 9.2.8 5.5.5 2.3z" fill="currentColor"/></svg>555 214-3086</li>
        <li><svg viewBox="0 0 10 10"><rect x="2.5" y=".8" width="5" height="8.4" rx="1" fill="none" stroke="currentColor" stroke-width="1.1"/></svg>555 739-4120</li>
        <li><svg viewBox="0 0 10 10"><rect x=".8" y="2" width="8.4" height="6" fill="currentColor"/><path d="M1 2.3l4 3 4-3" fill="none" stroke="#b01f24" stroke-width="1"/></svg>info@volbreyinc.example</li>
        <li><svg viewBox="0 0 10 10"><circle cx="5" cy="5" r="4.3" fill="currentColor"/><path d="M.8 5h8.4M5 .8c-2 2.5-2 5.9 0 8.4M5 .8c2 2.5 2 5.9 0 8.4" fill="none" stroke="#b01f24" stroke-width=".7"/></svg>www.volbreyinc.example</li>
      </ul>
    </div>
    <div class="front__disc"></div>
  </section>

  <section class="card card--back" aria-label="Card back">
    <div class="back__mark"></div>
    <div class="brand-name back__name">Volbrey Inc</div>
  </section>
</main>
</body>
</html>
```